Crypto currency project website revamp

Our current website is: http://www.kobaltchain.org

The new logo is also attached.

Here are some examples of the other crypto websites. Our goal is to re-make the above website to look and feel like the followings:

1) https://zyvanlabs.com/

2) https://tavo.io/

3) https://paylume.network/#/

Please submit your designs. Once we found the right design we need to interate a bit and add 3 or 4 more sections to it.

The coded website needs to be responsive

```html
<!DOCTYPE html>
<html lang="en">
<head>
<meta charset="utf-8">
<title>Kobalt Chain</title>
<link rel="stylesheet" href="https://fonts.googleapis.com/css2?family=Montserrat:wght@500;700;800&family=PT+Sans:wght@400;700&family=Open+Sans:wght@400;600;700&family=Work+Sans:wght@400;500;600&display=swap">
<style>
:root{
  --blue:#0a6fc2;
  --blue-deep:#0b4f94;
  --blue-dark:#063a70;
  --blue-btn:#0b5aa6;
  --ink:#3f3f3f;
  --muted:#555;
  --white:#fff;
  --light:#eef1f5;
}
*{margin:0;padding:0;box-sizing:border-box}
html,body{width:1200px;height:3719px;overflow:hidden}
body{position:relative;font-family:"Open Sans",sans-serif;color:var(--ink);background:var(--white)}
section,header,footer{position:absolute;left:0;width:1200px}
.abs{position:absolute}

/* hero */
.hero{top:0;height:585px;background:radial-gradient(ellipse at 55% 45%,#2f8fdb 0%,#1370c0 45%,#0a4f98 100%);color:var(--white)}
.brand{left:99px;top:32px;display:flex;align-items:center;gap:10px;font-family:"Montserrat",sans-serif;font-weight:700;font-size:21px;letter-spacing:.3px}
.brand-dot{width:22px;height:22px;border-radius:50%;background:var(--white)}
.nav{right:222px;top:39px;display:flex;gap:22px;font-family:"Open Sans",sans-serif;font-size:13px;white-space:nowrap}
.login{left:1012px;top:32px;width:90px;height:34px;border:2px solid var(--white);border-radius:17px;font-size:14px;font-weight:600;display:flex;align-items:center;justify-content:center}
.hero-title{left:0;width:1200px;top:158px;text-align:center;font-family:"Montserrat",sans-serif;font-weight:800;font-size:50px;line-height:68px;letter-spacing:1px}
.hero-text{left:230px;width:740px;top:306px;text-align:center;font-family:"Montserrat",sans-serif;font-weight:500;font-size:15px;line-height:29px}
.btn{height:56px;border-radius:28px;display:flex;align-items:center;justify-content:center;font-family:"Montserrat",sans-serif;font-weight:500;font-size:19px;letter-spacing:.5px}
.btn-ghost{left:383px;top:400px;width:203px;border:2px solid var(--white)}
.btn-solid{left:614px;top:400px;width:203px;background:var(--white);color:var(--blue)}
.scroll-down{left:573px;top:558px;width:54px;height:54px;border-radius:50%;background:var(--blue-deep);border:3px solid var(--white);z-index:2;display:flex;align-items:center;justify-content:center}

/* features */
.features{top:585px;height:746px}
.section-title{left:0;width:1200px;text-align:center;font-family:"PT Sans",sans-serif;font-weight:700;font-size:38px;color:#444}
.features .section-title{top:140px}
.features-intro{left:195px;width:810px;top:215px;text-align:center;font-size:12px;line-height:28px;color:#333}
.feature{width:300px;text-align:center}
.feature-icon{margin:0 auto;width:130px;height:130px;border:3px solid var(--blue);border-radius:50%;display:flex;align-items:center;justify-content:center}
.feature-name{margin-top:30px;font-family:"PT Sans",sans-serif;font-weight:700;font-size:18px;color:var(--blue)}
.feature-text{margin:14px auto 0;width:230px;font-size:12px;line-height:22px;color:#444}
.arrow{top:400px}

/* about */
.about{top:1331px;height:541px;background:linear-gradient(120deg,#0f7acd 0%,#0a65b7 60%,#0b5aa8 100%);color:var(--white)}
.about-title{left:99px;top:116px;font-family:"PT Sans",sans-serif;font-weight:700;font-size:37px}
.about-text{left:99px;top:172px;width:470px;font-size:12.5px;line-height:22px}
.about-text p+p{margin-top:14px}
.read-more{left:99px;top:375px;width:132px;height:48px;border-radius:24px;background:var(--blue-btn);box-shadow:0 4px 10px rgba(0,0,0,.2);display:flex;align-items:center;justify-content:center;font-family:"PT Sans",sans-serif;font-weight:700;font-size:15px}
.about-media{left:597px;top:114px;width:502px;height:313px;background:linear-gradient(135deg,#1b2d55 0%,#2c4f8a 40%,#b58a2a 62%,#2a5c98 100%)}

/* team */
.team{top:1872px;height:768px}
.team .section-title{top:146px;font-size:37px}
.team-sub{left:0;width:1200px;top:205px;text-align:center;font-family:"Work Sans",sans-serif;font-weight:500;font-size:16px;color:#555;letter-spacing:.3px}
.member{width:300px;top:306px;text-align:center}
.member-photo{margin:0 auto;width:240px;height:240px;border-radius:50%;border:6px solid var(--white);box-shadow:6px 8px 16px rgba(0,0,0,.3)}
.photo-1{background:linear-gradient(160deg,#dfe4ea,#8aa1c2)}
.photo-2{background:linear-gradient(160deg,#e8ddd0,#3a3d45)}
.photo-3{background:linear-gradient(160deg,#d9c2b0,#8cb3dc)}
.member-name{margin-top:26px;font-family:"Work Sans",sans-serif;font-weight:600;font-size:22px;color:#333}
.member-role{margin-top:8px;font-family:"Work Sans",sans-serif;font-size:14px;line-height:20px;color:#555}

/* resources */
.resources{top:2640px;height:451px;background:linear-gradient(180deg,#e6eaf0 0%,#f1f3f6 50%,#dde2e9 100%)}
.res-card{top:117px;height:228px;color:var(--white)}
.res-card .frame{position:absolute;inset:18px;border:2px solid rgba(255,255,255,.9)}
.res-card .label{position:absolute;left:0;right:0;top:100px;text-align:center;font-family:"Montserrat",sans-serif;font-weight:700;font-size:22px;letter-spacing:1px;text-shadow:0 2px 4px rgba(0,0,0,.35)}
.card-code{left:99px;width:316px;background:linear-gradient(135deg,#2b86d6,#0f4f9a)}
.card-paper{left:436px;width:325px;background:linear-gradient(135deg,#c9a24a,#8a6420 55%,#3b5fa0)}
.card-roadmap{left:781px;width:320px;background:linear-gradient(160deg,#4a6fc4,#14245c 60%,#0b1233)}

/* newsletter */
.newsletter{top:3091px;height:345px}
.newsletter .section-title{top:98px;font-size:36px}
.news-text{left:0;width:1200px;top:162px;text-align:center;font-size:13px;color:#333}
.subscribe{left:409px;top:209px;width:384px;height:44px;border:2px solid var(--blue-deep);border-radius:22px;overflow:hidden}
.subscribe .field{position:absolute;left:20px;top:12px;font-size:12px;color:#333}
.subscribe .go{position:absolute;right:0;top:0;width:117px;height:100%;background:var(--blue-deep);color:var(--white);border-radius:20px;display:flex;align-items:center;justify-content:center;font-weight:700;font-size:15px}

/* footer */
.site-footer{top:3436px;height:283px;background:linear-gradient(135deg,#0a62b3 0%,#0b5aa6 60%,#0c4f95 100%);color:var(--white)}
.col{top:58px}
.col h4{font-family:"PT Sans",sans-serif;font-weight:700;font-size:16px;margin-bottom:12px}
.col li{list-style:none;font-size:12px;line-height:24px;display:flex;align-items:center;gap:8px}
.col li .ind{width:14px;display:inline-flex;justify-content:center}
.social{display:flex;gap:15px}
.social span{width:32px;height:32px;border-radius:50%;background:var(--white);display:block}
.rule{left:99px;top:233px;width:1002px;height:1px;background:rgba(255,255,255,.45)}
.copy{left:0;width:1200px;top:250px;text-align:center;font-size:12px}
</style>
</head>
<body>

<header class="hero">
  <div class="abs brand"><span class="brand-dot"></span>KOBALT CHAIN</div>
  <nav class="abs nav"><span>Home</span><span>About Us</span><span>Codebase</span><span>Yellow Paper</span><span>Contact Us</span></nav>
  <div class="abs login">Login</div>
  <h1 class="abs hero-title">FUTURE OF CRYPTOCURRENCIES<br>WE WERE PROMISED</h1>
  <p class="abs hero-text">Lorem ipsum dolor sit amet, consectetur adipiscing elit, sed do eiusmod tempor incididunt ut labore et dolore magna aliqua Ut enim ad minim veniam quis nostrud</p>
  <div class="abs btn btn-ghost">LEARN MORE</div>
  <div class="abs btn btn-solid">BUY NOW</div>
</header>
<div class="abs scroll-down">
  <svg width="14" height="22" viewBox="0 0 14 22"><path d="M7 1v18M2 14l5 6 5-6" stroke="#fff" stroke-width="2.5" fill="none"/></svg>
</div>

<section class="features">
  <h2 class="abs section-title">Cryptocurrencies Booming</h2>
  <p class="abs features-intro">Kobalt is a peer-to-peer graph to exchange and transact most crypto-currencies with NO fee or counterparty risk. Kobalt is a decentralized, and distributed ledger technology with built-in support to read across chains. This means Kobalt is able to represent almost any crypto-currency and allow them to be exchanged and transacted in the Kobalt network.</p>
  <svg class="abs arrow" style="left:42px" width="16" height="20" viewBox="0 0 16 20"><path d="M12 3 5 10l7 7" stroke="#222" stroke-width="3" fill="none"/></svg>
  <svg class="abs arrow" style="left:1136px" width="16" height="20" viewBox="0 0 16 20"><path d="M4 3l7 7-7 7" stroke="#222" stroke-width="3" fill="none"/></svg>

  <div class="abs feature" style="left:99px;top:344px">
    <div class="feature-icon"><svg width="64" height="64" viewBox="0 0 64 64" fill="none" stroke="#0a6fc2" stroke-width="3"><circle cx="36" cy="20" r="11"/><circle cx="48" cy="32" r="7"/><path d="M6 44h12l10 4h14c3 0 3 5 0 5H28M18 44v12H6"/></svg></div>
    <div class="feature-name">Kobalt Coin</div>
    <p class="feature-text">Sed ut perspiciatis unde omnis iste natus error sit voluptatem accusan tium doloremque ipsam</p>
  </div>
  <div class="abs feature" style="left:445px;top:344px">
    <div class="feature-icon"><svg width="60" height="60" viewBox="0 0 60 60" fill="none" stroke="#0a6fc2" stroke-width="7" stroke-linecap="round"><path d="M26 34 34 26"/><path d="M22 30l-7 7a7 7 0 0 0 10 10l7-7"/><path d="M38 30l7-7a7 7 0 0 0-10-10l-7 7"/></svg></div>
    <div class="feature-name">Business Value</div>
    <p class="feature-text">Sed ut perspiciatis unde omnis iste natus error sit voluptatem accusan tium doloremque ipsam</p>
  </div>
  <div class="abs feature" style="left:790px;top:344px">
    <div class="feature-icon"><svg width="50" height="56" viewBox="0 0 50 56"><path d="M13 24V16a12 12 0 0 1 24 0v8" stroke="#0a6fc2" stroke-width="6" fill="none"/><rect x="5" y="24" width="40" height="30" rx="4" fill="#0a6fc2"/></svg></div>
    <div class="feature-name">Secure &amp; Decentralized</div>
    <p class="feature-text">Sed ut perspiciatis unde omnis iste natus error sit voluptatem accusan tium doloremque ipsam</p>
  </div>
</section>

<section class="about">
  <h2 class="abs about-title">About Kobalt Chain</h2>
  <div class="abs about-text">
    <p>Lorem Ipsum. Proin gravida nibh vel velit auctor aliquet. Aenean sollicitudin, ipsum, nec sagittis sem nibh id elit. Duis sed odio sit amet nibh vulputate cursus auctor a ornare odio. sed odio sit amet nibh vulputate cursus a sit amet mauris. Morbi accums an ipsum velit. Sed non mauris vitae erat.</p>
    <p>Lorem Ipsum. Proin gravida nibh vel velit auctor aliquet. Aenean sollicitudin, ipsum, nec sagittis sem nibh id elit. Duis sed odio sit amet nibh vulputate cursus auctor a ornare odio. sed odio sit amet nibh vulputate cursus a sit amet mauris.</p>
  </div>
  <div class="abs read-more">Read More</div>
  <div class="abs about-media" role="img" aria-label="Gold coin in front of a market chart with rising green line"></div>
</section>

<section class="team">
  <h2 class="abs section-title">Our Team</h2>
  <p class="abs team-sub">The world's most successful business teams</p>
  <div class="abs member" style="left:125px">
    <div class="member-photo photo-1" role="img" aria-label="Portrait of Marten Holloway"></div>
    <div class="member-name">Marten Holloway</div>
    <div class="member-role">Founder &amp;<br>General Manager</div>
  </div>
  <div class="abs member" style="left:450px">
    <div class="member-photo photo-2" role="img" aria-label="Portrait of Rafael Quinn"></div>
    <div class="member-name">Rafael Quinn</div>
    <div class="member-role">Information &amp;<br>Knowledge Manager</div>
  </div>
  <div class="abs member" style="left:775px">
    <div class="member-photo photo-3" role="img" aria-label="Portrait of Tobias Renner"></div>
    <div class="member-name">Tobias Renner</div>
    <div class="member-role">Information &amp;<br>Brand Manager</div>
  </div>
</section>

<section class="resources" role="img" aria-label="Faint background of keyboard and coin">
  <div class="abs res-card card-code" role="img" aria-label="Blue binary code backdrop"><div class="frame"></div><div class="label">CODEBASE</div></div>
  <div class="abs res-card card-paper" role="img" aria-label="Gold coin close-up backdrop"><div class="frame"></div><div class="label">YELLOW PAPER</div></div>
  <div class="abs res-card card-roadmap" role="img" aria-label="Space-themed roadmap timeline backdrop"><div class="frame"></div><div class="label">ROADMAP</div></div>
</section>

<section class="newsletter">
  <h2 class="abs section-title">Join Our Newsletter</h2>
  <p class="abs news-text">Lorem Ipsum is simply dummy text of the printing and typesetting industry.</p>
  <div class="abs subscribe"><span class="field">Enter your Email</span><span class="go">Subscribe</span></div>
</section>

<footer class="site-footer">
  <div class="abs col" style="left:99px">
    <h4>Contact</h4>
    <ul>
      <li><span class="ind"><svg width="12" height="11" viewBox="0 0 12 11"><path d="M6 0 0 5h2v6h3V7h2v4h3V5h2z" fill="#fff"/></svg></span>Kobalt Chain,</li>
      <li><span class="ind"></span>Lorem Ipsum is Simple</li>
      <li><span class="ind"><svg width="11" height="11" viewBox="0 0 11 11"><path d="M2 0l2 3-1 1.5c.8 1.5 2 2.7 3.5 3.5L8 7l3 2-1 2C5 11 0 6 0 1z" fill="#fff"/></svg></span>(+1) 555 010 2040</li>
      <li><span class="ind"><svg width="12" height="9" viewBox="0 0 12 9"><rect width="12" height="9" fill="#fff"/><path d="M0 0l6 5 6-5" stroke="#0b5aa6" fill="none"/></svg></span>mail@kobaltchain.org</li>
    </ul>
  </div>
  <div class="abs col" style="left:377px">
    <h4>Quick Links</h4>
    <ul><li>» How to get started</li><li>» Features</li><li>» Contact</li></ul>
  </div>
  <div class="abs col" style="left:630px">
    <h4>About Kobaltchain</h4>
    <ul><li>» Terms of service</li><li>» Legal notice</li><li>» Crypto Currency Briefs</li><li>» Documentation</li></ul>
  </div>
  <div class="abs col" style="left:922px">
    <h4>Follow Us On</h4>
    <div class="social" aria-label="Social profiles"><span></span><span></span><span></span><span></span></div>
  </div>
  <div class="abs rule"></div>
  <p class="abs copy">Copyright © 2018 Kobalt Chain. All Rights Reserved</p>
</footer>

</body>
</html>
```